Zielgruppe
Verkauf und Einbau von Fenstern, Haustüren, Rollläden, Raffstore, Markisen, Insektenschutzgitter, Plissees
Aufgabenstellung
Es soll das gleiche Farbschema meines Firmenlogos haben. Grauer Hintergrund, kleine gelbe Akzente und schwarze Schrift

```html
<!DOCTYPE html>
<html lang="de">
<head>
<meta charset="utf-8">
<title>Rahmenhaus – Über uns und Kontakt</title>
<link rel="stylesheet" href="https://fonts.googleapis.com/css2?family=Archivo:wght@700&family=Manrope:wght@400;500;700&family=Kaushan+Script&display=swap">
<style>
  :root {
    --canvas: #aeaeae;
    --paper: #f3f3f3;
    --heading: #4a2310;
    --accent-brown: #7a3a1c;
    --body: #555555;
    --yellow: #e8b815;
    --field: rgba(226, 170, 20, 0.72);
    --white: #ffffff;
  }
  * { margin: 0; padding: 0; box-sizing: border-box; }
  html, body { width: 1200px; height: 1200px; overflow: hidden; background: var(--canvas); }
  body { position: relative; font-family: "Manrope", sans-serif; }

  .panel { position: absolute; }
  .about { left: 179px; top: 0; width: 841px; height: 467px; background: var(--paper); }
  .about-photo {
    position: absolute; left: 502px; top: 0; width: 339px; height: 467px;
    background: linear-gradient(160deg, #8a4a24 0%, #b5743f 40%, #d9b28a 65%, #7a4326 100%);
  }
  .brand {
    position: absolute; left: 620px; top: 140px; display: flex; align-items: center; gap: 8px;
    font-family: "Manrope", sans-serif; font-weight: 700; font-size: 20px; color: var(--yellow); letter-spacing: 0.02em;
  }
  .brand-dot { width: 12px; height: 12px; border-radius: 50%; background: var(--yellow); }

  .section-title {
    position: absolute; font-family: "Archivo", sans-serif; font-weight: 700;
    font-size: 20px; line-height: 24.5px; letter-spacing: 0.2em; color: var(--heading); text-transform: uppercase;
  }
  .about .section-title { left: 56px; top: 53px; }

  .copy { position: absolute; font-size: 9.3px; line-height: 15.8px; color: var(--body); }
  .copy p + p { margin-top: 15.8px; }
  .copy-intro { left: 58px; top: 155px; width: 285px; }
  .copy-main { left: 58px; top: 200px; width: 285px; }
  .copy-main h3 { font-size: 13.5px; font-weight: 500; color: var(--accent-brown); line-height: 18px; margin-bottom: 2px; }

  .join-badge {
    position: absolute; left: 565px; top: 340px; width: 104px; height: 104px; border-radius: 50%;
    background: var(--yellow); color: var(--white); text-align: center;
    display: flex; flex-direction: column; justify-content: center; align-items: center;
  }
  .join-badge strong { font-weight: 700; font-size: 12.5px; line-height: 13.5px; }
  .join-badge em { font-family: "Kaushan Script", cursive; font-style: normal; font-size: 15px; margin-top: 4px; }

  .contact-form { left: 179px; top: 469px; width: 416px; height: 473px;
    background: radial-gradient(ellipse at 40% 10%, #b07a1a 0%, #5a3414 45%, #2a1a10 100%); }
  .field {
    position: absolute; background: var(--field); color: var(--white);
    font-weight: 700; font-size: 12.5px; padding-left: 26px; line-height: 26px; height: 26px;
  }
  .field-name { left: 68px; top: 81px; width: 134px; }
  .field-first { left: 213px; top: 81px; width: 133px; padding-left: 14px; }
  .field-mail { left: 68px; top: 128px; width: 278px; }
  .field-phone { left: 68px; top: 167px; width: 278px; }
  .field-message { left: 68px; top: 214px; width: 278px; height: 149px; line-height: 12.5px; padding-top: 12px; }
  .submit {
    position: absolute; left: 68px; top: 383px; width: 134px; height: 27px;
    border: 1.5px solid var(--white); color: var(--white); font-weight: 700; font-size: 12.5px;
    line-height: 24px; padding-left: 27px;
  }

  .contact-info { left: 595px; top: 469px; width: 425px; height: 473px; background: var(--paper); }
  .contact-info .section-title { left: 49px; top: 109px; }
  .copy-contact { left: 53px; top: 212px; width: 310px; }
  .details { position: absolute; font-size: 9.3px; line-height: 12.5px; color: var(--body); }
  .hours { left: 53px; top: 265px; }
  .hours td { padding: 0; vertical-align: top; }
  .hours td:first-child { width: 81px; }
  .location { left: 241px; top: 265px; }
  .location p + p { margin-top: 6px; }
  .reach { left: 53px; top: 349px; }
  .reach li { list-style: none; display: flex; align-items: center; gap: 4px; margin-bottom: 4.5px; }
  .reach svg { width: 11px; height: 11px; }
</style>
</head>
<body>

<section class="panel about">
  <h2 class="section-title">Wer wir sind?<br>Blicken Sie hinter<br>die Fassade.</h2>
  <div class="copy copy-intro">
    <p>Lorem ipsum dolor sit amet, consectetuer adipiscing elit, sed diam nonummy nibh euismod tincidunt ut laoreet dolor.</p>
  </div>
  <div class="copy copy-main">
    <h3>Lorem ipsum</h3>
    <p>Lorem ipsum dolor sit amet, consectetuer adipiscing elit, sed diam nonummy nibh euismod tincidunt ut laoreet dolore magna aliquam erat volutpat. Ut wisi enim ad minim veniam, quis nostrud exerci tation ullamcorper</p>
    <p>Lorem ipsum dolor sit amet, consectetuer adipiscing elit, sed diam nonummy nibh euismod tincidunt ut laoreet dolore magna aliquam erat volutpat. Ut wisi enim ad minim veniam, quis nostrud exerci tation ullamcorper nonummy nibh euismod tincidunt ut laoreet dolore magna aliquam erat volutpat. Ut wisi enim ad minim veniam, quis nostrud exerci tation ullamcorper</p>
  </div>
  <div class="about-photo" role="img" aria-label="Foto: lächelnder Handwerker in Latzhose vor einem Holzrahmenbau"></div>
  <div class="brand"><span class="brand-dot"></span>RAHMENHAUS</div>
  <div class="join-badge">
    <strong>Werde Teil<br>des Teams.</strong>
    <em>Bewirb dich!</em>
  </div>
</section>

<section class="panel contact-form" role="img" aria-label="Foto: Hände auf einer Laptop-Tastatur in warmem Licht">
  <div class="field field-name">Name</div>
  <div class="field field-first">Vorname</div>
  <div class="field field-mail">E-Mail Adresse</div>
  <div class="field field-phone">Telefonnummer</div>
  <div class="field field-message">Ihre Nachricht ...</div>
  <div class="submit">Kontaktieren</div>
</section>

<section class="panel contact-info">
  <h2 class="section-title">Kontaktieren Sie uns.<br>Wir freuen uns auf<br>Ihre Anfrage.</h2>
  <div class="copy copy-contact">
    <p>Lorem ipsum dolor sit amet, consectetuer adipiscing elit, sed diam nonummy nibh euismod tincidunt ut laoreet dolore magna aliquam erat volutpat.</p>
  </div>
  <table class="details hours">
    <tr><td colspan="2">Öffnungszeiten:</td></tr>
    <tr><td>Dienstag - Freitag:</td><td>17-23 Uhr</td></tr>
    <tr><td>Samstag:</td><td>17-0 Uhr</td></tr>
    <tr><td>Sonntag:</td><td>17 - 22 Uhr</td></tr>
    <tr><td>Montag:</td><td>Ruhetag</td></tr>
  </table>
  <div class="details location">
    <p>Hier findest du uns:</p>
    <p>Kupferkessel Stube<br>Lindenallee 14<br>04105 Leipzig</p>
  </div>
  <ul class="details reach">
    <li>
      <svg viewBox="0 0 16 16" fill="none" stroke="#555" stroke-width="1.2"><path d="M4 1.5l2.2 3-1.4 1.6c.8 1.8 2.3 3.3 4.1 4.1l1.6-1.4 3 2.2-1 2.5C8 13.5 2.5 8 2 2.5z"/></svg>
      0151 20 48 316
    </li>
    <li>
      <svg viewBox="0 0 16 16" fill="none" stroke="#555" stroke-width="1.2"><rect x="1.5" y="3.5" width="13" height="9"/><path d="M1.5 3.5L8 9l6.5-5.5M1.5 12.5l4.5-4.5M14.5 12.5L10 8"/></svg>
      kontakt@kupferkessel-stube.de
    </li>
  </ul>
</section>

</body>
</html>
```